Mobile Repair Service on location needs a Web Design

We are starting a new mobile device repair service called Handset Haven and our website needs a design!

Hello Designers!
First, we'd like to make clear this is more than a simple web design contest, we want the designers to create an idea. We want someone who can create the whole theme of the service's we provide. We want someone that can help design our visual branding, help us communicate a sentiment. And we are willing to pay for that.

Who are we?
Our company is based in Rotterdam, the Netherlands. We provide different services for all kinds of electronic devices. The kind of services we provide are, among other things, installations of hardware and software and the repair of broken or malfunctioning devices.
We are starting a new service that offers mobile device repairs on location, be it at the home of our customers, their office, or any other place. Just give us the address and we will come to you for the repair job. This is also our main USP. We have multiple skilled engineers who drive trough the country on a daily basis and can be on location within a working day. Repair is done immediately onsite while the customer waits. At this stage we will start with the smartphone product-group within the mobile devices. In a second phase we might also add tablets.
People don't want to be without their phone for weeks because of some parts that needed to be ordered by a repair center they had to sent their phone to. We offer a fully functional mobile repair center in the form of specially customized vans. These vans have all the tools and utilities needed by our engineers to safely repair your mobile device. Your phone is being repaired directly in front of you, the next business-day, on a location you desire.

For this new service we are creating a website called Handset Haven. The website needs a story and matching design and this is where you come in. We are not looking for a simple template design we can get from any place. We need a story. We want you to create an idea, build a unique theme or vision that helps sell the product/service. This goes beyond the design of the website. We need the whole package, the design you are creating needs to have returning elements like icons, color use, images, maybe even characters etc. You name it! There needs to be a common thread in the design so we can reuse elements in, for example, the email templates, the work order or receipt we give to our customers (we may contact the winner of the contest to design these for us as well!).

The name 'Handset Haven' is chosen. Rehab (short for rehabilitate) has a bold and playful tone to it and the design needs to reflect the name. So we're looking for a somewhat playful and cheeky design. Definitely not too serious and definitely modern. We already got a logo that we love and that fit's this description (see attached design documents for the logo). It's bold, powerful and fun. Our web design needs to reflect this as well and has to fit in with our logo.
We would really like it if the design somehow incorporates elements that highlight our unique selling points (repairs on location, we come to you etc.). We would really like some form of story telling in the design. Think clumsy people breaking their phones. Teenagers in tears because they have no access to their friends. People nowadays have the need to always be 'connected'. What happens when your phone is broken or malfunctioning? We're handling tech, we are nerds and a little bit weird, but we're professionals and here to help you with your problem. The sentiment Byte Brigade tries to communicate is something we really like. We're looking for fresh idea's, anything goes!

In an overview all Unique Selling Points of the Handset haven service:
- Professional service on location. Don’t ship to us we will come to you!
- Clear pricing upfront. No hidden cost.
- Next business-day repair.
- Backed by a professional call center open 12 hours a day and open on a Saturday as well
- Backed by a professional repair center with more then 12 years of experience
- Repair is done by certified engineers
- 1 year warranty on the repair

The process:
The main function of our website will be for customers to make a repair request. A customer will visit our website and can make a repair request immediately by going through a 'request-order-flow'. In this flow he or she will need to fill in some forms and can select wich type/model/brand of mobile device he or she has and what parts need to be repaired. After a request is placed we will call the customer back (within an hour) for a short intake and to set a date/time and location. Our engineer will meet the customer at the specified location and will repair the device onsite in one of our mobile repair centers, which is a specialized van equipped with all the tools needed for device restorations.
So in short the steps are:
- Choose your device and repair job
- Place the order
- Get a callback within the hour
- Set date and location
- We will come to you.

Website functionality:
Our website is our main form of communication. So the sentiment we want to communicate needs be reflected in the design. We need a main/front page designed (preferably a long scrolling page design) containing:
1. Customers will be able to request a repair job directly on our website. So there will need to be a prominent button/link at the top of our main page that will bring the customer to this 'request-order-flow'. This is the main flow which needs to be full focus on the front page. All other items are secondary.
2. The general information of who we are and what we do, and why the customer should choose us. Preferably in short bullet-point type keywords/sentences with icons or other visual cues. See our unique selling points to get an idea of the information that will be displayed here.
3. There needs to be a section that will explain the process (see above) of a repair request step-by- step, again in brief short key sentences and with (custom) icons.
4. There needs to be a section that explains to the customer he/she can always contact us if they are not sure what the problem is with their device, and for this reason are not sure what repair request they should order.
5. We want to implement some functionality that display customer ratings or customer reviews. So there needs to be room for some kind of widget of plugin we're going to implement which shows these reviews.
6. A 'For business section' where we will explain all the options we provide for corporate clients.
7. Social media links.
8. There needs to be a menu with buttons that leads to the all sections described in the previous points.

For now, we need a design for our front page. In the second phase, when we have picked our winner, we may ask the winner to design the page(s) for our request workflow as well.

EDIT:
Finally, we have a very specific order in mind for the different segments of our website. We would like you to add some more segments that were not in our original brief as well:

1. Top header with order/request button. (should instantly make clear our main USP, we do repairs on location)
2. Our process
3. Our unique selling points / why choose us
4. The kind of repairs we do (broken screens, broken batteries, water damage, broken camera's, no sound etc.)
5. A 'meet our team' section, where we introduce some of our engineers
6. A 'contact us for any questions' section/
7. Testimonials/user reviews
8. A section where we show key performance indicators
9. 'For businesses' sections
10.'Subscribe for newsletter' field
11. Social media buttons

Industry/Entity Type

It Service

Number of Pages Required

1 page

Font styles to use
Sans Serif

Requirements
Must have
• a main/front page, design only
• custom icons/images for banners, adverts online and in print (high res)
Nice to have
• Storytelling in our design.
• Design that fits with our brand new logo.
• Elements like icons to have a flat design.
• Keep in mind that the website will need to be responsive when designing! (Ideally provide an example of the mobile design as well)
• Create a fun and trustworthy feeling.

```html
<!DOCTYPE html>
<html lang="en">
<head>
<meta charset="utf-8">
<title>Handset Haven — Repair &amp; Installation</title>
<link href="https://fonts.googleapis.com/css2?family=Montserrat:wght@400;500;600;700&family=Open+Sans:ital,wght@0,400;0,600;0,700;1,400&display=swap" rel="stylesheet">
<style>
:root{
  --orange:#f26522;
  --orange-light:#fb8c1e;
  --orange-deep:#f0551c;
  --ink:#333333;
  --muted:#6d6d6d;
  --nav:#5a5a5a;
  --nav-line:#6c6c6c;
  --light:#ececec;
  --footer:#222222;
  --white:#ffffff;
}
*{box-sizing:border-box;margin:0;padding:0}
html,body{width:1200px;height:2894px;overflow:hidden}
body{font-family:"Open Sans",Arial,sans-serif;color:var(--ink);background:var(--white);position:relative}
section,header,footer,nav{position:absolute;left:0;width:1200px}

/* header */
.site-header{top:0;height:124px;background:var(--white)}
.brand{position:absolute;left:139px;top:34px;display:flex;align-items:center;gap:12px}
.brand-dot{width:52px;height:52px;border-radius:50%;background:var(--orange)}
.brand-name{font-family:"Montserrat",sans-serif;font-weight:700;font-size:22px;line-height:24px;color:var(--ink);width:110px}
.search{position:absolute;left:386px;top:46px;width:353px;height:37px;border:1px solid #cfcfcf;border-radius:3px;display:flex;align-items:center;padding-left:12px;gap:10px;font-size:13px;color:#999}
.header-links{position:absolute;right:130px;top:26px;display:flex;gap:34px}
.header-link{display:flex;flex-direction:column;align-items:center;gap:8px;font-size:14px;color:var(--orange)}
.header-link .ico{width:34px;height:34px;border:2px solid var(--orange);border-radius:50%;display:flex;align-items:center;justify-content:center}

/* nav */
.main-nav{top:124px;height:54px;background:var(--nav)}
.main-nav ul{list-style:none;position:absolute;left:139px;top:0;display:flex;height:54px}
.main-nav li{font-family:"Montserrat",sans-serif;font-weight:600;font-size:15px;color:var(--white);display:flex;align-items:center;justify-content:center;border-right:1px solid var(--nav-line);height:54px}
.main-nav li.active{background:var(--orange)}

/* hero */
.hero{top:178px;height:494px;background:linear-gradient(90deg,#f1f1f1 0%,#dcdcdc 55%,#c9c9c9 100%)}
.hero-photo{position:absolute;left:480px;top:0;width:720px;height:494px;background:radial-gradient(ellipse at 50% 55%,#5b7fb0 0%,#8fa6c4 30%,rgba(210,210,210,0) 65%)}
.hero-copy{position:absolute;left:139px;top:130px;width:520px}
.hero-title{font-family:"Montserrat",sans-serif;font-weight:600;font-size:42px;color:#555;letter-spacing:.5px}
.hero-sub{font-family:"Montserrat",sans-serif;font-weight:600;font-size:30px;color:var(--orange);margin-top:2px}
.hero-text{font-size:14px;line-height:22px;color:#666;margin-top:14px;width:450px}
.dots{display:flex;gap:8px;margin-top:18px}
.dots span{width:13px;height:13px;border-radius:50%;background:#9a9a9a}
.dots span:first-child{background:none;border:2px solid #9a9a9a}

/* about */
.about{top:672px;height:347px;text-align:center}
.section-title{font-family:"Montserrat",sans-serif;font-weight:500;font-size:33px;color:var(--ink)}
.about .section-title{margin-top:50px}
.about p{width:820px;margin:26px auto 0;font-size:14px;line-height:27px;color:var(--muted)}
.btn{display:inline-block;background:var(--orange);color:var(--white);font-family:"Montserrat",sans-serif;font-weight:600;font-size:11px;border-radius:3px;text-align:center}
.about .btn{position:absolute;left:538px;top:264px;width:118px;height:34px;line-height:34px}

/* process */
.process{top:1019px;height:336px;background:linear-gradient(180deg,var(--orange-light) 0%,var(--orange-deep) 100%);text-align:center}
.notch{position:absolute;left:574px;top:0;width:0;height:0;border-left:26px solid transparent;border-right:26px solid transparent;border-top:26px solid var(--white)}
.process .section-title{color:var(--white);font-size:26px;font-weight:400;margin-top:42px}
.step{position:absolute;top:102px;width:180px;margin-left:-90px;color:var(--white)}
.pin{width:94px;height:94px;margin:0 auto;border-radius:50% 50% 50% 0;transform:rotate(-45deg);background:#fca319;display:flex;align-items:center;justify-content:center}
.pin svg{transform:rotate(45deg)}
.step-label{font-family:"Montserrat",sans-serif;font-weight:600;font-size:16px;line-height:22px;margin-top:28px}
.flow-arrow{position:absolute;top:140px}

/* features */
.features{top:1355px;height:392px}
.feature{position:absolute;top:46px;width:222px;height:301px;background:var(--white);box-shadow:0 1px 4px rgba(0,0,0,.25)}
.feature-photo{height:159px}
.feature p{padding:14px 20px 0;font-size:14px;line-height:21px;font-weight:600;color:var(--ink)}
.feature .more{position:absolute;left:20px;bottom:20px;font-family:"Montserrat",sans-serif;font-size:10px;font-weight:600;color:var(--orange)}

/* how we work */
.how{top:1747px;height:424px;background:var(--light)}
.how-photo{position:absolute;right:0;top:0;width:683px;height:424px;clip-path:polygon(81px 0,683px 0,683px 424px,0 424px);background:linear-gradient(135deg,#8797a9 0%,#d8dde3 45%,#b9c2cc 100%)}
.how-copy{position:absolute;left:133px;top:78px;width:410px}
.how-copy .section-title{font-size:29px;font-weight:400}
.how-copy p{font-size:13px;line-height:23px;color:var(--muted);margin-top:18px}
.how-copy .btn{margin-top:14px;width:118px;height:36px;line-height:36px}

/* testimonials */
.testimonials{top:2171px;height:392px;text-align:center}
.testimonials .section-title{color:var(--orange);font-size:25px;font-weight:400;margin-top:46px}
.review{position:absolute;top:126px;width:300px}
.review-box{height:166px;border:1px solid #d6d6d6;padding:50px 26px 0;font-size:12px;line-height:22px;font-style:italic;color:var(--muted)}
.avatar{position:absolute;left:117px;top:-34px;width:66px;height:66px;border-radius:50%;border:3px solid #fff;box-shadow:0 0 0 1px #d6d6d6}
.author{font-size:15px;margin-top:12px;color:var(--ink)}
.city{font-size:11px;margin-top:4px;color:#555}

/* footer */
.site-footer{top:2563px;height:331px;background:var(--footer);color:#bdbdbd}
.f-col{position:absolute;top:48px}
.f-col h4{font-family:"Montserrat",sans-serif;font-weight:400;font-size:21px;color:var(--white);margin-bottom:10px}
.f-col li{list-style:none;font-size:13px;line-height:29px}
.signup input{display:block;width:222px;height:32px;border:0;padding-left:14px;font-size:12px;font-family:inherit}
.signup .btn{margin-top:12px;width:108px;height:32px;line-height:32px}
.socials{display:flex;gap:11px;margin-top:4px}
.socials span{width:34px;height:34px;border-radius:50%;background:#5c5c5c}
.footer-rule{position:absolute;left:139px;top:264px;width:922px;height:1px;background:#444}
.copyright{position:absolute;top:286px;width:1200px;text-align:center;font-size:12px}
</style>
</head>
<body>

<header class="site-header">
  <div class="brand"><span class="brand-dot"></span><span class="brand-name">Handset Haven</span></div>
  <div class="search">
    <svg width="16" height="16" viewBox="0 0 16 16"><circle cx="6.5" cy="6.5" r="5" fill="none" stroke="#f26522" stroke-width="2"/><line x1="10" y1="10" x2="15" y2="15" stroke="#f26522" stroke-width="2"/></svg>
    Enter Keyword here
  </div>
  <div class="header-links">
    <div class="header-link"><span class="ico"><svg width="16" height="16" viewBox="0 0 16 16"><circle cx="8" cy="5" r="3.5" fill="#f26522"/><path d="M1 16c0-4 3-6 7-6s7 2 7 6z" fill="#f26522"/></svg></span>My Account</div>
    <div class="header-link"><span class="ico"><svg width="18" height="16" viewBox="0 0 18 16"><path d="M1 1h3l2 9h9l2-7H5" fill="none" stroke="#f26522" stroke-width="2"/><circle cx="7" cy="14" r="1.5" fill="#f26522"/><circle cx="14" cy="14" r="1.5" fill="#f26522"/></svg></span>My Cart</div>
    <div class="header-link"><span class="ico"><svg width="16" height="16" viewBox="0 0 16 16"><path d="M2 2h12v9H7l-4 3v-3H2z" fill="#f26522"/></svg></span>Order &amp; Store</div>
  </div>
</header>

<nav class="main-nav">
  <ul>
    <li class="active" style="width:118px">HOME</li>
    <li style="width:123px">ABOUT US</li>
    <li style="width:126px">SERVICES</li>
    <li style="width:164px">HOW IT WORK</li>
    <li style="width:137px">SOLUTION</li>
    <li style="width:116px">WHY US</li>
    <li style="width:148px;border-right:0">CONTACT US</li>
  </ul>
</nav>

<section class="hero">
  <div class="hero-photo" role="img" aria-label="Smiling technician in a blue checked shirt giving two thumbs up"></div>
  <div class="hero-copy">
    <h1 class="hero-title">REPAIR &amp; INSTALLATION</h1>
    <h2 class="hero-sub">HARDWARE AND SOFTWARE</h2>
    <p class="hero-text">Praesent sit amet est In dictum dolor eu dictum porttitor enim felis viverra mi eget luctus massa purus quis odio</p>
    <div class="dots"><span></span><span></span><span></span><span></span></div>
  </div>
</section>

<section class="about">
  <h2 class="section-title">WHO ARE WE?</h2>
  <p>Our company is based in Rotterdam, the Netherlands. We provide different services for all kinds of electronic devices. The kind of services we provide are, among other things, installations of hardware and software and the repair of broken or malfunctioning devices. We are starting a new service that offers mobile device repairs on location,be it at the home of our customers, their office, or any other place. Just give us the address and we will come to you for the repair job.</p>
  <span class="btn">READ MORE</span>
</section>

<section class="process">
  <span class="notch"></span>
  <h2 class="section-title">OUR PROCESS</h2>

  <div class="step" style="left:259px">
    <div class="pin"><svg width="44" height="40" viewBox="0 0 44 40" fill="none" stroke="#fff" stroke-width="3"><rect x="6" y="4" width="32" height="22"/><path d="M2 32h40"/><path d="M16 18l5-6 4 4 5-6"/></svg></div>
    <div class="step-label">Choose your device<br>and repair job</div>
  </div>
  <div class="step" style="left:442px">
    <div class="pin"><svg width="44" height="40" viewBox="0 0 44 40" fill="none" stroke="#fff" stroke-width="3"><path d="M22 3l9 5v10l-9 5-9-5V8z"/><path d="M12 19l9 5v10l-9 5-9-5V24z"/><path d="M32 19l9 5v10l-9 5-9-5V24z"/></svg></div>
    <div class="step-label">Place the order</div>
  </div>
  <div class="step" style="left:621px">
    <div class="pin"><svg width="40" height="40" viewBox="0 0 40 40" fill="none" stroke="#fff" stroke-width="3"><path d="M8 4l7 7-4 5c3 6 7 10 13 13l5-4 7 7-5 5C18 36 4 22 3 9z"/><path d="M24 8a10 10 0 0 1 8 8"/><path d="M24 2a16 16 0 0 1 14 14"/></svg></div>
    <div class="step-label">Get a callback<br>within the hour</div>
  </div>
  <div class="step" style="left:803px">
    <div class="pin"><svg width="40" height="40" viewBox="0 0 40 40" fill="none" stroke="#fff" stroke-width="3"><rect x="4" y="7" width="32" height="29"/><path d="M4 15h32M12 3v8M28 3v8"/><circle cx="20" cy="25" r="4"/></svg></div>
    <div class="step-label">Set date and<br>location</div>
  </div>
  <div class="step" style="left:973px">
    <div class="pin"><svg width="40" height="40" viewBox="0 0 40 40"><circle cx="20" cy="20" r="17" fill="#fff"/><path d="M12 20l6 6 11-12" fill="none" stroke="#fca319" stroke-width="4"/></svg></div>
    <div class="step-label">We will come<br>to you.</div>
  </div>

  <svg class="flow-arrow" style="left:320px" width="72" height="24" viewBox="0 0 72 24" fill="none" stroke="#fff" stroke-width="2"><path d="M2 20Q36 -4 66 14"/><path d="M58 14h9v-8"/></svg>
  <svg class="flow-arrow" style="left:502px" width="72" height="24" viewBox="0 0 72 24" fill="none" stroke="#fff" stroke-width="2"><path d="M2 20Q36 -4 66 14"/><path d="M58 14h9v-8"/></svg>
  <svg class="flow-arrow" style="left:682px" width="72" height="24" viewBox="0 0 72 24" fill="none" stroke="#fff" stroke-width="2"><path d="M2 20Q36 -4 66 14"/><path d="M58 14h9v-8"/></svg>
  <svg class="flow-arrow" style="left:856px" width="72" height="24" viewBox="0 0 72 24" fill="none" stroke="#fff" stroke-width="2"><path d="M2 20Q36 -4 66 14"/><path d="M58 14h9v-8"/></svg>
</section>

<section class="features">
  <article class="feature" style="left:137px">
    <div class="feature-photo" role="img" aria-label="Hands repairing an open phone circuit board with pliers" style="background:linear-gradient(135deg,#2d3336,#6b7a70)"></div>
    <p>Professional service on location. Don't ship to us we will come to you!</p>
    <span class="more">CLICK HERE &rsaquo;</span>
  </article>
  <article class="feature" style="left:372px">
    <div class="feature-photo" role="img" aria-label="Smiling technician at a workbench" style="background:linear-gradient(135deg,#e4e6e8,#aab3bb)"></div>
    <p>Clear pricing upfront. No hidden cost.</p>
    <span class="more">CLICK HERE &rsaquo;</span>
  </article>
  <article class="feature" style="left:606px">
    <div class="feature-photo" role="img" aria-label="Disassembled phone parts and screwdrivers on a repair mat" style="background:linear-gradient(135deg,#c9ced3,#5f6b78)"></div>
    <p>Backed by a professional repair center with more then 12 years of experience</p>
    <span class="more">CLICK HERE &rsaquo;</span>
  </article>
  <article class="feature" style="left:841px">
    <div class="feature-photo" role="img" aria-label="Call center agent wearing a headset" style="background:linear-gradient(135deg,#eceff1,#b8a79a)"></div>
    <p>Backed by a professional call center open 12 hours a day and open on saturday</p>
    <span class="more">CLICK HERE &rsaquo;</span>
  </article>
</section>

<section class="how">
  <div class="how-copy">
    <h2 class="section-title">HOW WE WORK</h2>
    <p>People don't want to be without their phone for weeks because of some parts that needed to be ordered by a repair center they had to sent their phone to. We offer a fully functional mobile repair center in the form of specially customized vans. These vans have all the tools and utilities needed by our engineers to safely repair your mobile device. Your phone is being repaired directly in front of you, the next business-day, on a location you desire.</p>
    <span class="btn">READ MORE</span>
  </div>
  <div class="how-photo" role="img" aria-label="Gloved hands holding a smartphone over a repair bench with tools"></div>
</section>

<section class="testimonials">
  <h2 class="section-title">TESTIMONIALS</h2>
  <div class="review" style="left:137px">
    <div class="review-box">Morbi diam mauris viverra in gravida eu mattis in ante Morbi eget arcu Morbi porta libero id ullamcorper nonummy nibh ligula pulvinar metus eget consectetuer</div>
    <span class="avatar" role="img" aria-label="Customer portrait" style="background:#c9a58a"></span>
    <div class="author">By Author Name</div><div class="city">City Location</div>
  </div>
  <div class="review" style="left:450px">
    <div class="review-box">Praesent sit amet est In dictum dolor eu dictum porttitor enim felis viverra mi eget luctus massa purus quis odio</div>
    <span class="avatar" role="img" aria-label="Customer portrait" style="background:#7fc4c9"></span>
    <div class="author">By Author Name</div><div class="city">City Location</div>
  </div>
  <div class="review" style="left:762px">
    <div class="review-box">Morbi diam mauris viverra in gravida eu mattis in ante Morbi eget arcu Morbi porta libero id ullamcorper nonummy nibh ligula pulvinar metus eget consectetuer</div>
    <span class="avatar" role="img" aria-label="Customer portrait" style="background:#d8c2a8"></span>
    <div class="author">By Author Name</div><div class="city">City Location</div>
  </div>
</section>

<footer class="site-footer">
  <div class="f-col" style="left:143px"><h4>Quick Links</h4><ul><li>About Us</li><li>What We Do</li><li>Why We Are</li><li>Blogs</li></ul></div>
  <div class="f-col" style="left:305px"><h4>Our Services</h4><ul><li>Morbi diam</li><li>Aauris viverra</li><li>Gravida eu</li><li>Pattis in ante</li></ul></div>
  <div class="f-col" style="left:481px"><h4>Resources</h4><ul><li>FAQ</li><li>Testimonials</li><li>Contact Us</li></ul></div>
  <div class="f-col signup" style="left:639px"><h4>Sign Up Email</h4><input type="email" placeholder="Email address"><span class="btn">SUBSCRIBE</span></div>
  <div class="f-col" style="left:892px"><h4>Get in touch</h4><div class="socials"><span></span><span></span><span></span><span></span></div></div>
  <div class="footer-rule"></div>
  <p class="copyright">&copy; 2017 Company Name &nbsp;All right reserved &nbsp;Term of Use</p>
</footer>

</body>
</html>
```